Specialised investor in e-mobility and energy wants business card design

We need a business card design that fits our existing corporate design. <The look and feel must be 'sharp'/'clean', dynamic, communicate momentum, professionalism etc (as one would imagine from a firm in the financial sector). We like the idea of a reverse-side of the card that includes the logo, and the name and contact details on the other. We expect the deliverable to be whatever format might be required to be able to get cards printed directly by a service such as kelmo press. Our website is www.zub.capital

```html
<!DOCTYPE html>
<html lang="en">
<head>
<meta charset="utf-8">
<title>Zub Capital – Business Card</title>
<link href="https://fonts.googleapis.com/css2?family=Montserrat:wght@400;500;700&display=swap" rel="stylesheet">
<style>
  :root {
    --bg: #2a2a2a;
    --card-white: #ffffff;
    --green-dark: #344f24;
    --green-deep: #2d4a1e;
    --green-light: #8bbd4a;
    --ink: #2b2b2b;
    --radius: 21px;
  }
  * { margin: 0; padding: 0; box-sizing: border-box; }
  html, body { width: 1200px; height: 1059px; overflow: hidden; }
  body {
    background: var(--bg);
    font-family: "Montserrat", sans-serif;
    position: relative;
  }
  .card {
    position: absolute;
    border-radius: var(--radius);
    overflow: hidden;
  }
  .card-front {
    left: 256px; top: 89px; width: 688px; height: 390px;
    background: var(--card-white);
  }
  .card-back {
    left: 254px; top: 547px; width: 693px; height: 393px;
    background: var(--green-dark);
    display: flex; align-items: center; justify-content: center;
  }
  .wordmark {
    font-weight: 500;
    letter-spacing: 0.5px;
    white-space: nowrap;
  }
  .card-front .wordmark {
    position: absolute; left: 39px; top: 64px;
    font-size: 40px; color: var(--green-deep);
  }
  .card-back .wordmark {
    font-size: 72px; color: #ffffff;
  }
  .holder {
    position: absolute; right: 36px; top: 62px; text-align: right;
  }
  .holder-name {
    font-size: 26px; font-weight: 700; letter-spacing: 1px;
    color: var(--green-deep); line-height: 1.1;
  }
  .holder-name .surname { color: var(--green-light); }
  .holder-title {
    font-size: 16px; color: var(--ink); margin-top: 4px;
  }
  .accent-bar {
    position: absolute; right: 0; top: 64px;
    width: 18px; height: 42px; background: var(--green-light);
  }
  .address {
    position: absolute; left: 39px; top: 218px;
    font-size: 15px; line-height: 22px; color: var(--ink); letter-spacing: 0.5px;
  }
  .contacts {
    position: absolute; left: 39px; top: 278px;
    list-style: none; font-size: 16px; color: var(--ink); letter-spacing: 0.5px;
  }
  .contacts li {
    display: flex; align-items: center; gap: 9px; height: 27.5px;
  }
  .contacts svg { width: 12px; height: 12px; fill: var(--green-light); flex: none; }
</style>
</head>
<body>
  <section class="card card-front">
    <div class="wordmark">Zub Capital</div>
    <div class="holder">
      <div class="holder-name">MARTEN <span class="surname">OLBREY</span></div>
      <div class="holder-title">Director/Founder</div>
    </div>
    <div class="accent-bar"></div>
    <address class="address" style="font-style:normal">
      1234 Street Name<br>
      Country Name AB 5748
    </address>
    <ul class="contacts">
      <li>
        <svg viewBox="0 0 24 24" aria-hidden="true"><path d="M6.6 10.8a15.1 15.1 0 0 0 6.6 6.6l2.2-2.2a1 1 0 0 1 1-.25 11.4 11.4 0 0 0 3.6.57 1 1 0 0 1 1 1V20a1 1 0 0 1-1 1A17 17 0 0 1 3 4a1 1 0 0 1 1-1h3.5a1 1 0 0 1 1 1c0 1.25.2 2.45.57 3.57a1 1 0 0 1-.25 1z"/></svg>
        123-480-2917
      </li>
      <li>
        <svg viewBox="0 0 24 24" aria-hidden="true"><path d="M2 5h20v14H2z M2 5l10 7 10-7" /><path d="M2 6.5l10 7 10-7V5H2z" fill="#fff" opacity="0.6"/></svg>
        info@zub.capital
      </li>
      <li>
        <svg viewBox="0 0 24 24" aria-hidden="true"><circle cx="12" cy="12" r="10"/><path d="M7 7c2 1 3 3 2 5s1 4 3 5M14 4c-1 2 0 3 2 4s3 2 2 4" stroke="#fff" stroke-width="1.6" fill="none"/></svg>
        &nbsp;www.zub.capital
      </li>
    </ul>
  </section>

  <section class="card card-back">
    <div class="wordmark">Zub Capital</div>
  </section>
</body>
</html>
```